Architectural, Engineering and Design Build

Tovandex4.com
Veteran Disabled Certified company is doing business in Architecture, Engineer and Design build - look simialr websites and come up with design follow following website
https://hollis-darnet.example/
https://www.venlorcogroup.example/
https://www.pembrisgc.example/contract-vehicles/service-disabled-veteran-owned-small-business-sdvosb/
https://www.corbelnetlink.example/about/sdvosb/

Target Market(s)

US - Defense and Federal Government

Industry/Entity Type

Colors
0054AA
0677BA
7BADD7
CADEEF
E8F1F8

Requirements
Must have
• Army, American patriotism , Buildings, construction, architecture, engineering
Nice to have
• I need to attract federal government agencies and Defense

```html
<!DOCTYPE html>
<html lang="en">
<head>
<meta charset="utf-8">
<title>Tovandex4 – Architecture, Engineering &amp; Design Build</title>
<link href="https://fonts.googleapis.com/css2?family=Montserrat:ital,wght@0,400;0,500;0,600;0,700;1,500;1,600&display=swap" rel="stylesheet">
<style>
:root{
  --navy:#141f5e;
  --navy-deep:#0d1648;
  --red:#d71f27;
  --blue:#0054aa;
  --blue-mid:#0677ba;
  --blue-soft:#7badd7;
  --blue-pale:#cadeef;
  --blue-mist:#e8f1f8;
  --white:#ffffff;
  --ink:#1c2030;
  --grey:#5a6072;
}
*{box-sizing:border-box;margin:0;padding:0}
html,body{width:1200px;height:4180px;overflow:hidden}
body{font-family:"Montserrat",Arial,sans-serif;color:var(--ink);background:var(--white);position:relative}
section,header,footer{position:absolute;left:0;width:1200px;overflow:hidden}
.btn{position:absolute;display:flex;align-items:center;justify-content:center;gap:14px;background:var(--red);color:var(--white);font-weight:600;font-size:20px;letter-spacing:.5px;text-transform:uppercase}
.btn svg{width:28px;height:14px}
.ghost-word{position:absolute;left:0;width:1200px;text-align:center;font-weight:700;font-size:130px;letter-spacing:12px;color:rgba(255,255,255,.04)}
.ghost-word.dark{color:rgba(20,31,94,.05)}

/* hero */
.hero{top:0;height:620px;background:linear-gradient(180deg,#1b2a72 0%,#2b4a9a 45%,#1a2a6e 100%)}
.hero-sky{position:absolute;left:250px;top:0;width:700px;height:620px;background:linear-gradient(180deg,rgba(123,173,215,.55),rgba(6,119,186,.25) 60%,rgba(20,31,94,0));}
.hero-person{position:absolute;bottom:0;width:330px;height:560px;background:linear-gradient(180deg,#7a7f62 0%,#5d6350 55%,#3f4436 100%);border-radius:160px 160px 0 0}
.hero-person.left{left:20px}
.hero-person.right{right:20px}
.nav{position:absolute;top:70px;left:0;width:1200px;height:40px}
.nav a{position:absolute;color:var(--white);font-size:18px;font-weight:500;text-decoration:none;text-transform:uppercase}
.brand{position:absolute;left:500px;top:22px;width:200px;height:110px;display:flex;flex-direction:column;align-items:center;justify-content:center;gap:6px}
.brand .dot{width:44px;height:44px;border-radius:50%;background:var(--red)}
.brand .name{color:var(--white);font-weight:700;font-size:30px;letter-spacing:1px}
.hero h1{position:absolute;top:176px;left:0;width:1200px;text-align:center;color:var(--white);font-size:44px;font-weight:700;letter-spacing:1px}
.hero .lead{position:absolute;top:262px;left:330px;width:540px;text-align:center;color:var(--white);font-size:24px;font-weight:600;line-height:56px;text-transform:uppercase}
.hero .btn{left:486px;top:488px;width:228px;height:54px}

/* about */
.about{top:620px;height:850px;background:var(--navy)}
.about .eyebrow{position:absolute;left:110px;top:118px;color:var(--white);font-size:18px;font-weight:700}
.about h2{position:absolute;left:110px;top:168px;color:var(--white);font-size:26px;font-weight:500;letter-spacing:.5px;text-transform:uppercase}
.about h2 em{font-style:italic}
.about p{position:absolute;left:110px;top:226px;width:510px;color:var(--white);font-size:16px;line-height:30px}
.about .btn{left:110px;top:460px;width:230px;height:56px}
.about-photo{position:absolute;left:648px;top:120px;width:410px;height:410px;border-radius:50%;border:6px solid var(--red);padding:18px;background:var(--white)}
.about-photo div{width:100%;height:100%;border-radius:50%;background:linear-gradient(160deg,#e6ebf2 0%,#b9c6d6 50%,#7f95ad 100%)}
.stats{position:absolute;left:90px;top:600px;width:1040px;display:flex}
.stat{width:310px;color:var(--white)}
.stat b{display:block;font-size:56px;font-weight:400}
.stat span{display:block;margin-top:30px;font-size:20px;text-transform:uppercase}
.about .ghost-word{top:720px}

/* why */
.why{top:1470px;height:870px;background:var(--white)}
.collage{position:absolute;left:-20px;top:80px;width:560px;height:680px}
.tile{position:absolute;width:250px;height:250px;transform:rotate(45deg);border:6px solid var(--white)}
.t1{left:160px;top:40px;background:linear-gradient(135deg,#8a6a4a,#c9a57a)}
.t2{left:0;top:220px;background:linear-gradient(135deg,#7a6a52,#b4a27e)}
.t3{left:300px;top:220px;background:linear-gradient(135deg,#eef1f4,#a9b3bf)}
.t4{left:160px;top:400px;background:linear-gradient(135deg,#6fa6dc,#2e64ad)}
.why .eyebrow{position:absolute;left:630px;top:90px;font-size:18px;font-weight:600;color:var(--navy)}
.why h2{position:absolute;left:630px;top:128px;font-size:36px;font-weight:600;color:var(--navy)}
.why h2 em{font-style:italic;font-weight:500}
.why .intro{position:absolute;left:630px;top:196px;width:480px;font-size:16px;line-height:28px;color:var(--grey)}
.feature{position:absolute;left:630px;width:500px;height:110px}
.feature .icon{position:absolute;left:0;top:0;width:66px;height:66px;border-radius:50%;background:var(--navy);display:flex;align-items:center;justify-content:center}
.feature .icon svg{width:30px;height:30px}
.feature h3{position:absolute;left:110px;top:4px;font-size:18px;font-weight:600;color:var(--navy)}
.feature p{position:absolute;left:110px;top:36px;width:380px;font-size:16px;line-height:28px;color:var(--grey)}
.feature-line{position:absolute;left:662px;top:320px;width:2px;height:270px;background:var(--navy)}
.why .btn{left:630px;top:710px;width:358px;height:58px}
.why .ghost-word{top:740px}

/* services */
.services{top:2340px;height:770px;background:var(--navy)}
.services h2{position:absolute;top:66px;left:0;width:1200px;text-align:center;color:var(--white);font-size:36px;font-weight:600}
.services h2 em{font-style:italic;font-weight:500}
.arrow-nav{position:absolute;top:360px;width:40px;height:20px}
.service{position:absolute;top:170px;width:300px}
.service .photo{width:270px;height:270px;border-radius:50%;margin-left:15px}
.service h3{margin-top:40px;color:var(--white);font-size:18px;font-weight:600;text-transform:uppercase}
.service p{margin-top:12px;color:var(--white);font-size:16px;line-height:28px}
.service .btn{position:relative;margin-top:22px;width:150px;height:40px;font-size:15px;gap:10px}
.service .btn svg{width:22px;height:12px}
.services .ghost-word{top:640px}

/* consultation */
.consult{top:3110px;height:610px;background:linear-gradient(180deg,#1f83cf 0%,#63aee4 55%,#bfdcf2 85%,#d8c79c 100%)}
.consult h2{position:absolute;left:110px;top:94px;color:var(--white);font-size:36px;font-weight:600;text-transform:uppercase}
.consult h2 em{font-style:italic;font-weight:500}
.field{position:absolute;height:66px;background:var(--white);border-bottom:6px solid var(--navy);padding:22px 0 0 20px;font-size:16px;font-weight:500;color:var(--ink)}
.field svg{position:absolute;right:16px;top:22px;width:20px;height:20px}
.consult .btn{left:110px;top:468px;width:492px;height:56px;font-size:20px}
.consult-photo{position:absolute;left:700px;top:210px;width:480px;height:400px;background:linear-gradient(180deg,rgba(120,130,110,0) 0%,rgba(120,120,90,.55) 60%,#b9a06a 100%);border-radius:220px 220px 0 0}

/* footer */
.footer{top:3720px;height:460px;background:var(--white)}
.footer-brand{position:absolute;left:110px;top:80px;width:170px;display:flex;flex-direction:column;align-items:center;gap:8px}
.footer-brand .dot{width:46px;height:46px;border-radius:50%;background:var(--red)}
.footer-brand .name{font-size:28px;font-weight:700;color:var(--navy)}
.socials{position:absolute;left:110px;top:210px;display:flex;gap:10px}
.socials span{width:32px;height:32px;border-radius:50%;border:2px solid var(--navy)}
.copyright{position:absolute;left:110px;top:272px;font-size:16px;font-weight:600;color:var(--navy)}
.col{position:absolute;top:100px}
.col h4{font-size:20px;font-weight:700;color:var(--navy);text-transform:uppercase;margin-bottom:22px}
.col li{list-style:none;font-size:15px;color:var(--ink);line-height:30px;text-transform:uppercase}
.contact{position:absolute;left:860px;width:300px}
.contact svg{position:absolute;left:0;top:0;width:26px;height:26px}
.contact h4{margin-left:54px;font-size:20px;font-weight:700;color:var(--navy);text-transform:uppercase}
.contact p{margin:18px 0 0 54px;font-size:15px;line-height:30px;color:var(--ink);text-transform:uppercase}
</style>
</head>
<body>

<header class="hero">
  <div class="hero-sky" role="img" aria-label="Glass office towers seen from below against a blue sky"></div>
  <div class="hero-person left" role="img" aria-label="Smiling female soldier in camouflage uniform"></div>
  <div class="hero-person right" role="img" aria-label="Smiling male soldier in camouflage uniform"></div>
  <nav class="nav">
    <a style="left:272px">Home</a>
    <a style="left:368px">About us</a>
    <a style="left:728px">Our services</a>
    <a style="left:898px">Contact us</a>
  </nav>
  <div class="brand"><span class="dot"></span><span class="name">TOVANDEX4</span></div>
  <h1>WELCOME TO TOVANDEX4</h1>
  <p class="lead">We are a veteran disabled certified company is doing business in architecture</p>
  <a class="btn">Get started <svg viewBox="0 0 28 14"><path d="M0 7h25M19 1l6 6-6 6" fill="none" stroke="#fff" stroke-width="2"/></svg></a>
</header>

<section class="about">
  <div class="eyebrow">WELCOME TO TOVANDEX4</div>
  <h2>Veteran disabled <em>certified</em> company</h2>
  <p>Lorem ipsum dolor sit amet, consectetur adipiscing elit, sed do eiusmod tempor incididunt ut labore et dolore magna aliqua. Ut enim ad minim veniam, quis nostrud exercitation ullamco laboris nisi ut aliquip ex ea commodo consequat. Duis aute irure dolor in reprehenderit in voluptate velit esse cillum dolore eu fugiat nulla pariatur.</p>
  <a class="btn">Learn more <svg viewBox="0 0 28 14"><path d="M0 7h25M19 1l6 6-6 6" fill="none" stroke="#fff" stroke-width="2"/></svg></a>
  <div class="about-photo"><div role="img" aria-label="White house porch with an American flag on the column"></div></div>
  <div class="stats">
    <div class="stat"><b>41</b><span>Years in business</span></div>
    <div class="stat"><b>89%</b><span>Repeat business</span></div>
    <div class="stat" style="width:420px"><b>45%</b><span>Professional certifications</span></div>
  </div>
  <div class="ghost-word">TOVANDEX4</div>
</section>

<section class="why">
  <div class="collage">
    <div class="tile t1" role="img" aria-label="Wooden porch with American flag"></div>
    <div class="tile t2" role="img" aria-label="Soldiers marching in the desert"></div>
    <div class="tile t3" role="img" aria-label="Modern white building exterior"></div>
    <div class="tile t4" role="img" aria-label="Glass skyscrapers against blue sky"></div>
  </div>
  <div class="eyebrow">WHY CHOOSE US ?</div>
  <h2>WHAT MAKES US <em>DIFFERENT</em></h2>
  <p class="intro">Lorem ipsum dolor sit amet, consectetur adipiscing elit, sed do eiusmod tempor incididunt.</p>
  <div class="feature-line"></div>
  <div class="feature" style="top:300px">
    <div class="icon"><svg viewBox="0 0 30 30"><path d="M15 3l10 4v8c0 6-4 10-10 12C9 25 5 21 5 15V7z" fill="none" stroke="#fff" stroke-width="2"/><path d="M10 15l4 4 6-7" fill="none" stroke="#fff" stroke-width="2"/></svg></div>
    <h3>LOREM IPSUM DOLOR</h3>
    <p>Lorem ipsum dolor sit amet, consectetur adipiscing elit, sed do</p>
  </div>
  <div class="feature" style="top:440px">
    <div class="icon"><svg viewBox="0 0 30 30"><rect x="7" y="4" width="16" height="23" fill="none" stroke="#fff" stroke-width="2"/><path d="M11 9h3M16 9h3M11 14h3M16 14h3M11 19h3M16 19h3" stroke="#fff" stroke-width="2"/></svg></div>
    <h3>LOREM IPSUM DOLOR</h3>
    <p>Lorem ipsum dolor sit amet, consectetur adipiscing elit, sed do</p>
  </div>
  <div class="feature" style="top:580px">
    <div class="icon"><svg viewBox="0 0 30 30"><circle cx="11" cy="12" r="5" fill="none" stroke="#fff" stroke-width="2"/><circle cx="20" cy="20" r="4" fill="none" stroke="#fff" stroke-width="2"/></svg></div>
    <h3>LOREM IPSUM DOLOR</h3>
    <p>Lorem ipsum dolor sit amet, consectetur adipiscing elit, sed do</p>
  </div>
  <a class="btn">Get free consultation <svg viewBox="0 0 28 14"><path d="M0 7h25M19 1l6 6-6 6" fill="none" stroke="#fff" stroke-width="2"/></svg></a>
  <div class="ghost-word dark">TOVANDEX4</div>
</section>

<section class="services">
  <h2>OUR <em>SERVICES</em></h2>
  <svg class="arrow-nav" style="left:30px" viewBox="0 0 40 20"><path d="M38 10H4M10 3L3 10l7 7" fill="none" stroke="#fff" stroke-width="2"/></svg>
  <svg class="arrow-nav" style="left:1120px" viewBox="0 0 40 20"><path d="M2 10h34M30 3l7 7-7 7" fill="none" stroke="#fff" stroke-width="2"/></svg>
  <div class="service" style="left:110px">
    <div class="photo" role="img" aria-label="Bright modern interior with large windows" style="background:linear-gradient(160deg,#f2f2f2,#bdbdbd)"></div>
    <h3>Architecture &amp; Interiors</h3>
    <p>Lorem ipsum dolor sit amet, consectetur adipiscing elit, sed do</p>
    <a class="btn">Read more <svg viewBox="0 0 22 12"><path d="M0 6h19M14 1l5 5-5 5" fill="none" stroke="#fff" stroke-width="2"/></svg></a>
  </div>
  <div class="service" style="left:460px">
    <div class="photo" role="img" aria-label="Project team meeting around a table" style="background:linear-gradient(160deg,#d9d6d0,#7c7367)"></div>
    <h3>Project management</h3>
    <p>Lorem ipsum dolor sit amet, consectetur adipiscing elit, sed do</p>
    <a class="btn">Read more <svg viewBox="0 0 22 12"><path d="M0 6h19M14 1l5 5-5 5" fill="none" stroke="#fff" stroke-width="2"/></svg></a>
  </div>
  <div class="service" style="left:800px">
    <div class="photo" role="img" aria-label="Engineer in hard hat and safety vest on site" style="background:linear-gradient(160deg,#f6d35a,#b7c93f 50%,#6f8a3a)"></div>
    <h3>Engineering</h3>
    <p>Lorem ipsum dolor sit amet, consectetur adipiscing elit, sed do</p>
    <a class="btn">Read more <svg viewBox="0 0 22 12"><path d="M0 6h19M14 1l5 5-5 5" fill="none" stroke="#fff" stroke-width="2"/></svg></a>
  </div>
  <div class="ghost-word">TOVANDEX4</div>
</section>

<section class="consult">
  <h2>REQUEST A <em>CONSULTATION</em></h2>
  <div class="field" style="left:110px;top:184px;width:240px">FIRST NAME*<svg viewBox="0 0 20 20"><circle cx="10" cy="6" r="4" fill="#141f5e"/><path d="M2 19c0-5 4-7 8-7s8 2 8 7z" fill="#141f5e"/></svg></div>
  <div class="field" style="left:362px;top:184px;width:240px">LAST NAME*<svg viewBox="0 0 20 20"><circle cx="10" cy="6" r="4" fill="#141f5e"/><path d="M2 19c0-5 4-7 8-7s8 2 8 7z" fill="#141f5e"/></svg></div>
  <div class="field" style="left:110px;top:264px;width:240px">PHONE*<svg viewBox="0 0 20 20"><path d="M4 2l4 1 1 4-2 2c1 2 3 4 5 5l2-2 4 1 1 4-2 2C9 19 1 11 2 4z" fill="#141f5e"/></svg></div>
  <div class="field" style="left:362px;top:264px;width:240px">EMAIL*<svg viewBox="0 0 20 20"><rect x="1" y="4" width="18" height="12" fill="#141f5e"/><path d="M1 4l9 7 9-7" fill="none" stroke="#fff" stroke-width="1.5"/></svg></div>
  <div class="field" style="left:110px;top:344px;width:492px;height:110px">MESSAGE*<svg viewBox="0 0 20 20"><path d="M2 3h16v10H8l-4 4v-4H2z" fill="#141f5e"/></svg></div>
  <a class="btn">Send a message <svg viewBox="0 0 28 14"><path d="M0 7h25M19 1l6 6-6 6" fill="none" stroke="#fff" stroke-width="2"/></svg></a>
  <div class="consult-photo" role="img" aria-label="Soldier and child holding an American flag in a field"></div>
</section>

<footer class="footer">
  <div class="footer-brand"><span class="dot"></span><span class="name">TOVANDEX4</span></div>
  <div class="socials"><span></span><span></span><span></span><span></span></div>
  <div class="copyright">@2024 COPYRIGHTS</div>
  <div class="col" style="left:390px"><h4>Links</h4><ul><li>Home</li><li>About us</li><li>Why choose us</li><li>Services</li><li>Contact us</li></ul></div>
  <div class="col" style="left:646px"><h4>Useful links</h4><ul><li>Disclaimer</li><li>Privacy policy</li><li>Terms of use</li><li>Sitemap</li></ul></div>
  <div class="contact" style="top:100px"><svg viewBox="0 0 26 26"><path d="M5 2l5 1 1 5-3 2c2 3 4 5 7 7l2-3 5 1 1 5-3 3C11 24 1 14 2 5z" fill="#141f5e"/></svg><h4>Call us</h4><p>+1 888 888 8888</p></div>
  <div class="contact" style="top:190px"><svg viewBox="0 0 26 26"><rect x="1" y="5" width="24" height="16" fill="#141f5e"/><path d="M1 5l12 9 12-9" fill="none" stroke="#fff" stroke-width="2"/></svg><h4>Mail us</h4><p>INFO@TOVANDEX4.EXAMPLE</p></div>
  <div class="contact" style="top:280px"><svg viewBox="0 0 26 26"><path d="M13 1c5 0 8 4 8 8 0 6-8 16-8 16S5 15 5 9c0-4 3-8 8-8z" fill="#141f5e"/><circle cx="13" cy="9" r="3" fill="#fff"/></svg><h4>Reach us</h4><p>34, Tovandex4 Lorem<br>902 892</p></div>
</footer>

</body>
</html>
```